Automotive eCommerce Business looking for a business card design

Looking for a clean and simple business card design. Our company name is "Brindle Auto" and we are a company specializing in the ecommerce sales of automotive parts, specifically for pick up trucks and large SUVs. Our company colours are red, black, and white.

Feel free to use the logo provided or create a new logo that you seem fit. Looking forward to your creative ideas!

Industry/Entity Type

Automotive

Contact Information for Business Card

We were thinking of a possibly two-sided design featuring just the logo and company name on one side, and personal information on the other side. Single sided designs will be considered as well.

Font styles to use
Serif
Sans Serif
Decorative

Colors
ec1f27
ffffff
000000

Requirements
Must have
• Space for employee's name, title, phone number and email address, along with the company address and website somewhere.

```html
<!DOCTYPE html>
<html lang="en">
<head>
<meta charset="utf-8">
<title>Brindle Auto Ltd — Business Card</title>
<link href="https://fonts.googleapis.com/css2?family=Cinzel:wght@400&family=Roboto:wght@400&display=swap" rel="stylesheet">
<style>
  :root {
    --backdrop: #262626;
    --card-white: #f4f4f4;
    --panel-grey: #4f5353;
    --brand-red: #a31d22;
    --ink-grey: #555555;
    --text-white: #ffffff;
  }
  * { margin: 0; padding: 0; box-sizing: border-box; }
  html, body {
    width: 1200px; height: 960px; overflow: hidden;
    background: var(--backdrop);
  }
  .canvas { position: relative; width: 1200px; height: 960px; }

  .card {
    position: absolute; left: 320px; width: 598px;
    border-radius: 14px; overflow: hidden;
    background: var(--card-white);
  }
  .card--front { top: 95px; height: 350px; }
  .card--back { top: 493px; height: 342px; }

  /* Front */
  .brand-mark {
    position: absolute; left: 34px; top: 150px;
    display: flex; align-items: center; gap: 16px;
  }
  .brand-mark__square { width: 34px; height: 34px; background: var(--brand-red); }
  .brand-mark__name {
    font-family: "Cinzel", serif; font-weight: 400;
    font-size: 40px; color: var(--brand-red); white-space: nowrap;
  }
  .front-signature {
    position: absolute; right: 33px; top: 275px; text-align: right;
  }
  .front-signature__name {
    font-family: "Cinzel", serif; font-size: 22px; color: var(--ink-grey);
  }
  .front-signature__web {
    margin-top: 4px;
    font-family: "Roboto", sans-serif; font-size: 13px;
    letter-spacing: 3.4px; color: var(--ink-grey);
  }

  /* Back */
  .back-panel { position: absolute; inset: 0; }
  .person { position: absolute; left: 34px; top: 28px; }
  .person__name {
    font-family: "Roboto", sans-serif; font-size: 19px;
    color: var(--brand-red); text-transform: uppercase;
  }
  .person__title {
    margin-top: 4px;
    font-family: "Roboto", sans-serif; font-size: 14px; color: var(--text-white);
  }
  .address {
    position: absolute; left: 34px; top: 171px;
    font-family: "Roboto", sans-serif; font-size: 14px; line-height: 18px;
    color: var(--text-white); font-style: normal;
  }
  .contacts {
    position: absolute; left: 34px; top: 217px; list-style: none;
    font-family: "Roboto", sans-serif; font-size: 14px; color: var(--text-white);
  }
  .contacts li { display: flex; align-items: center; height: 19px; }
  .contacts svg { width: 13px; height: 13px; margin-right: 10px; fill: var(--brand-red); }
  .back-brand {
    position: absolute; left: 240px; width: 390px; top: 118px;
    display: flex; flex-direction: column; align-items: center;
  }
  .back-brand__square { width: 40px; height: 40px; background: var(--brand-red); }
  .back-brand__name {
    margin-top: 82px;
    font-family: "Cinzel", serif; font-size: 22px; color: var(--ink-grey); white-space: nowrap;
  }
</style>
</head>
<body>
<main class="canvas">

  <section class="card card--front" aria-label="Card front">
    <div class="brand-mark">
      <span class="brand-mark__square"></span>
      <span class="brand-mark__name">Brindle Auto</span>
    </div>
    <div class="front-signature">
      <p class="front-signature__name">Brindle Auto Ltd</p>
      <p class="front-signature__web">www.brindleauto.com</p>
    </div>
  </section>

  <section class="card card--back" aria-label="Card back">
    <svg class="back-panel" viewBox="0 0 598 342" width="598" height="342" aria-hidden="true">
      <polygon points="0,0 390,0 257,107 257,252 395,342 0,342" fill="var(--panel-grey)"/>
    </svg>

    <div class="person">
      <p class="person__name">Owen Carter</p>
      <p class="person__title">CEO/FOUNDER</p>
    </div>

    <address class="address">214 Harbor Ridge Road<br>Juneau, Alaska 99801</address>

    <ul class="contacts">
      <li><svg viewBox="0 0 16 16"><path d="M3 1l3 3-2 2c1 2 3 4 5 5l2-2 3 3-2 3C6 15 1 10 0 3z"/></svg>555 210 4871</li>
      <li><svg viewBox="0 0 16 16"><path d="M4 0h8v16H4zM6 2v10h4V2z"/></svg>555 318 6042</li>
      <li><svg viewBox="0 0 16 16"><path d="M4 1h8v4H4zM1 6h14v8H1zM4 10h8v5H4z"/></svg>555 742 1936</li>
      <li><svg viewBox="0 0 16 16"><path d="M0 3h16v2L8 9 0 5zM0 7l8 4 8-4v7H0z"/></svg>owen@brindleauto.com</li>
      <li><svg viewBox="0 0 16 16"><circle cx="8" cy="8" r="7"/><path d="M1 8h14M8 1v14" stroke="#4f5353" stroke-width="1.4"/></svg>www.brindleauto.com</li>
    </ul>

    <div class="back-brand">
      <span class="back-brand__square"></span>
      <span class="back-brand__name">Brindle Auto Ltd.</span>
    </div>
  </section>

</main>
</body>
</html>
```